Veldmark Supplies Business Card

Professional business card that stand out to our potential customers. Front and back with clean modern design

Industry/Entity Type

Oil and gas

Contact Information for Business Card

Name, address, website , office phone and cell number

Requirements
Must have
• Editable files for each employee

```html
<!DOCTYPE html>
<html lang="en">
<head>
<meta charset="utf-8">
<title>Veldmark Supplies Business Card</title>
<link rel="stylesheet" href="https://fonts.googleapis.com/css2?family=Arimo:wght@400;700&display=swap">
<style>
  :root {
    --backdrop: #3c3c3c;
    --card-dark: #2a2a2a;
    --card-dark-deep: #222222;
    --brand-cyan: #00afd3;
    --accent-red: #e8141c;
    --text-white: #ffffff;
    --silver: #b4b4b4;
    --emboss: #3a3a3a;
  }
  * { box-sizing: border-box; margin: 0; padding: 0; }
  html, body { width: 1200px; height: 803px; overflow: hidden; }
  body {
    background: var(--backdrop);
    font-family: "Arimo", Arial, sans-serif;
    position: relative;
  }
  .card {
    position: absolute;
    top: 253px;
    width: 520px;
    height: 297px;
    border-radius: 18px;
    overflow: hidden;
    background: var(--card-dark);
  }
  .card--front { left: 60px; }
  .card--back { left: 620px; background: var(--card-dark-deep); }

  .front-panel { position: absolute; inset: 0; }

  .wordmark {
    position: absolute;
    left: 32px;
    top: 32px;
    font-weight: 700;
    font-size: 17px;
    letter-spacing: 1.5px;
    text-transform: uppercase;
    color: var(--text-white);
  }
  .holder { position: absolute; left: 32px; top: 92px; color: var(--text-white); }
  .holder-name { font-weight: 700; font-size: 24px; letter-spacing: 0.5px; text-transform: uppercase; }
  .holder-role { font-size: 13px; margin-top: 3px; }

  .address { position: absolute; left: 32px; top: 158px; color: var(--text-white); font-size: 13px; line-height: 16px; }

  .contact-list { position: absolute; left: 32px; top: 200px; list-style: none; color: var(--text-white); font-size: 13px; line-height: 16px; }
  .contact-list li { display: flex; align-items: center; gap: 7px; }
  .contact-list svg { width: 10px; height: 10px; flex: none; }

  .front-brand {
    position: absolute;
    right: 22px;
    top: 62px;
    width: 124px;
    text-align: center;
    color: var(--silver);
  }
  .brand-dot { display: block; margin: 0 auto 12px; width: 60px; height: 60px; border-radius: 50%; background: var(--silver); }
  .brand-name { font-weight: 700; font-size: 15px; letter-spacing: 1.5px; text-transform: uppercase; line-height: 19px; }

  .back-brand {
    position: absolute;
    inset: 0;
    display: flex;
    flex-direction: column;
    align-items: center;
    justify-content: center;
    gap: 18px;
    color: var(--silver);
  }
  .back-brand .brand-dot { width: 80px; height: 80px; margin: 0; background: var(--emboss); }
  .back-brand .brand-name { font-size: 24px; letter-spacing: 3px; line-height: 28px; }
</style>
</head>
<body>
  <section class="card card--front" aria-label="Business card front">
    <svg class="front-panel" viewBox="0 0 520 297" aria-hidden="true">
      <rect width="520" height="297" fill="var(--brand-cyan)"/>
      <polygon points="300,0 520,0 520,297 400,297" fill="var(--card-dark)"/>
    </svg>
    <div class="wordmark">Veldmark Supplies</div>
    <div class="holder">
      <div class="holder-name">Arlo Brennick</div>
      <div class="holder-role">President</div>
    </div>
    <div class="address">
      <p>412 Cedarline Road</p>
      <p>Halvern, Canada 20918</p>
    </div>
    <ul class="contact-list">
      <li>
        <svg viewBox="0 0 10 10"><path d="M2 1 L4 1 L4.5 3 L3.3 4 Q4.5 6 6 6.7 L7 5.5 L9 6 L9 8 Q9 9 8 9 Q1 8.5 1 2 Q1 1 2 1Z" fill="var(--accent-red)"/></svg>
        555-210-4471
      </li>
      <li>
        <svg viewBox="0 0 10 10"><rect x="1" y="1" width="8" height="8" fill="none" stroke="var(--accent-red)" stroke-width="1.4"/></svg>
        555-210-4489
      </li>
      <li>
        <svg viewBox="0 0 10 10"><rect x="0.5" y="0.5" width="9" height="9" fill="var(--accent-red)"/><path d="M2.5 5 L4.3 7 L7.7 3" fill="none" stroke="var(--text-white)" stroke-width="1.3"/></svg>
        info@veldmarksupplies.com
      </li>
      <li>
        <svg viewBox="0 0 10 10"><circle cx="5" cy="5" r="4.5" fill="var(--accent-red)"/><path d="M0.5 5 H9.5 M5 0.5 Q2.5 5 5 9.5 M5 0.5 Q7.5 5 5 9.5" fill="none" stroke="var(--text-white)" stroke-width="0.7"/></svg>
        www.veldmarksupplies.com
      </li>
    </ul>
    <div class="front-brand">
      <span class="brand-dot"></span>
      <div class="brand-name">Veldmark<br>Supplies</div>
    </div>
  </section>

  <section class="card card--back" aria-label="Business card back">
    <div class="back-brand">
      <span class="brand-dot"></span>
      <div class="brand-name">Veldmark Supplies</div>
    </div>
  </section>
</body>
</html>
```